Professional Services - letterhead / business cards

The company (velmora partners) will provide services to Investment Funds and large investors in Spain. I have recently chosen a logo that I am attaching.

I would like a simple stationary design that i could use as letter head, business cards and "with compliments" cards.

I am not quite sure which color I will mostly use for the logo, in the email signature I will probably lean towards the white background and grey letters. I am attaching my favourite options.

Target Market(s)

Large Multinationals, Investment funds and Law firms

Industry/Entity Type

Business

Requirements
Must have
• my details are:
Luis R. Abadal
Velmora Partners S.L.
Casa de Torrelumbre
Calle de Vientoalto 27
28014 Madrid
T: +34 (91) 387-2265
M: +34 (646) 819-054
e-mail: labadal@velmorapartners.com

```html
<!DOCTYPE html>
<html lang="en">
<head>
<meta charset="utf-8">
<title>Velmora Partners – Business Cards</title>
<link href="https://fonts.googleapis.com/css2?family=Carlito:wght@400;700&display=swap" rel="stylesheet">
<style>
  :root {
    --canvas: #e9e7e4;
    --card: #ffffff;
    --navy: #1c1f6e;
    --grey-text: #6d6d72;
    --rule: #b9b9bd;
    --shadow: rgba(0, 0, 0, 0.18);
  }
  * { box-sizing: border-box; margin: 0; padding: 0; }
  html, body {
    width: 1200px; height: 588px; overflow: hidden;
    background: var(--canvas);
    font-family: "Carlito", "Calibri", sans-serif;
  }
  .stage {
    position: relative; width: 1200px; height: 588px;
    display: flex; align-items: center; justify-content: center; gap: 60px;
  }
  .card {
    position: relative; width: 510px; height: 291px;
    background: var(--card);
    box-shadow: 0 6px 18px var(--shadow);
  }

  /* Front */
  .card-front .wordmark {
    position: absolute; left: 0; right: 0; top: 108px;
    text-align: center; color: var(--navy);
    font-size: 44px; font-weight: 400; letter-spacing: 0.5px;
  }
  .card-front .website {
    position: absolute; left: 0; right: 0; top: 176px;
    text-align: center; color: var(--navy);
    font-size: 13px; letter-spacing: 3.2px; font-style: italic;
  }

  /* Back */
  .card-back .wordmark {
    position: absolute; left: 70px; top: 30px;
    color: var(--navy); font-size: 34px; font-weight: 400;
  }
  .card-back .divider {
    position: absolute; left: 0; top: 0; width: 510px; height: 291px;
  }
  .holder {
    position: absolute; right: 34px; top: 120px; text-align: right;
  }
  .holder-name {
    color: var(--navy); font-size: 19px; letter-spacing: 1px; text-transform: uppercase;
  }
  .holder-company {
    color: var(--grey-text); font-size: 12px; margin-top: 4px;
  }
  .contacts {
    position: absolute; left: 40px; top: 160px; list-style: none;
    color: var(--grey-text); font-size: 13.5px;
  }
  .contacts li {
    display: flex; align-items: center; gap: 8px; height: 19px;
  }
  .contacts svg { width: 11px; height: 11px; fill: var(--navy); flex: none; }
  .address {
    position: absolute; right: 40px; top: 204px; text-align: right;
    color: var(--grey-text); font-size: 13.5px; line-height: 18px;
    font-style: normal;
  }
</style>
</head>
<body>
<main class="stage">

  <section class="card card-front" aria-label="Business card front">
    <p class="wordmark">velmora partners</p>
    <p class="website">www.velmorapartners.com</p>
  </section>

  <section class="card card-back" aria-label="Business card back">
    <p class="wordmark">velmora partners</p>

    <svg class="divider" viewBox="0 0 510 291" aria-hidden="true">
      <polyline points="0,95 330,120 490,120" fill="none" stroke="var(--rule)" stroke-width="1.3"/>
      <line x1="480" y1="150" x2="510" y2="150" stroke="var(--rule)" stroke-width="1.3"/>
    </svg>

    <div class="holder">
      <p class="holder-name">Luis R. Abadal</p>
      <p class="holder-company">Velmora Partners S.L.</p>
    </div>

    <ul class="contacts">
      <li>
        <svg viewBox="0 0 12 12" aria-hidden="true"><circle cx="6" cy="6" r="6"/><path d="M3.6 3.2c.4-.4.9-.3 1.1.1l.5.9c.2.4 0 .7-.3.9.3.8.9 1.4 1.7 1.8.2-.3.5-.5.9-.3l.9.5c.4.2.5.7.1 1.1-1.6 1.3-5.7-2.4-4.9-5z" fill="#fff"/></svg>
        +34 (91) 387-2265
      </li>
      <li>
        <svg viewBox="0 0 12 12" aria-hidden="true"><rect x="3" y="0.5" width="6" height="11" rx="1.2"/><rect x="4" y="2" width="4" height="6" fill="#fff"/></svg>
        +34 (646) 819-054
      </li>
      <li>
        <svg viewBox="0 0 12 12" aria-hidden="true"><rect x="0.5" y="2.5" width="11" height="7.5" rx="1"/><polyline points="1,3 6,7 11,3" fill="none" stroke="#fff" stroke-width="1"/></svg>
        labadal@velmorapartners.com
      </li>
    </ul>

    <address class="address">
      Casa de Torrelumbre<br>
      Calle de Vientoalto 27<br>
      28014 Madrid
    </address>
  </section>

</main>
</body>
</html>
```